Modern Business Card for Larkwell 2018

Our company assumes the best about people. We are creating an online community of entrepreneurs and business leaders who struggle with marketing their business online.

This business card should POP! We recently got a new logo and are launching a new website next month, so our business cards should make a statement that feels:
-Fresh
-Smart
-Trustworthy
-Fun

Target Market(s)

small business owners, entrepreneurs

Industry/Entity Type

Digital Marketing

Contact Information for Business Card

Dimensions: 3.5" x 2"

Font styles to use
Sans Serif

Colors
f37122
ffffff

Requirements
Must have
• We need a business card with a modern, bold design. We will use one side of the card as a lead-generation offer, so text on one side will need to fit up to 140 characters. The business card should stick to our core colors (orange, black, and white).
Nice to have
• We think a vertical "portrait" design could be interesting.
Should not have
• Should not look like a traditional business card. The round icon should stand out from a distance.

```html
<!DOCTYPE html>
<html lang="en">
<head>
<meta charset="utf-8">
<title>Larkwell Business Card</title>
<link rel="stylesheet" href="https://fonts.googleapis.com/css2?family=Roboto:wght@400;500;700&family=Alex+Brush&display=swap">
<style>
  :root {
    --brand-orange: #f37122;
    --card-white: #f7f7f7;
    --ink: #1f1f1f;
    --rule: #555555;
    --backdrop: #e3e3e3;
    --white: #ffffff;
  }
  * { margin: 0; padding: 0; box-sizing: border-box; }
  html, body { width: 1200px; height: 960px; overflow: hidden; }
  body {
    background: var(--backdrop);
    font-family: "Roboto", Arial, sans-serif;
    position: relative;
  }
  .card {
    position: absolute;
    width: 600px;
    height: 343px;
    background: var(--card-white);
    box-shadow: 0 4px 14px rgba(0,0,0,0.12);
    overflow: hidden;
  }
  /* Front */
  .card-front { left: 302px; top: 118px; }
  .person-name {
    position: absolute;
    left: 50px;
    top: 36px;
    font-family: "Alex Brush", cursive;
    font-size: 50px;
    line-height: 1;
    color: var(--brand-orange);
  }
  .contact-email {
    position: absolute;
    right: 47px;
    top: 67px;
    font-size: 15px;
    color: var(--ink);
  }
  .name-rule {
    position: absolute;
    left: 50px;
    right: 47px;
    top: 90px;
    height: 1px;
    background: var(--rule);
  }
  .job-title {
    position: absolute;
    left: 51px;
    top: 106px;
    font-size: 15px;
    font-weight: 500;
    letter-spacing: 0.3px;
    color: var(--ink);
  }
  .brand-dot {
    position: absolute;
    left: 477px;
    top: 230px;
    width: 70px;
    height: 70px;
    border-radius: 50%;
    background: var(--brand-orange);
  }
  /* Back */
  .card-back { left: 299px; top: 499px; }
  .offer-band {
    position: absolute;
    left: 0; top: 0;
    width: 600px; height: 219px;
    background: var(--brand-orange);
    color: var(--white);
  }
  .brand-lockup {
    position: absolute;
    left: 40px;
    width: 240px;
    top: 60px;
    text-align: center;
  }
  .brand-lockup .lockup-dot {
    display: block;
    width: 40px; height: 40px;
    border-radius: 50%;
    background: var(--white);
    margin: 0 auto 12px;
  }
  .brand-name {
    font-size: 37px;
    font-weight: 700;
    letter-spacing: 1px;
    line-height: 1;
  }
  .brand-tagline {
    margin-top: 7px;
    font-size: 11px;
    font-weight: 500;
    letter-spacing: 1px;
    text-transform: uppercase;
  }
  .band-divider {
    position: absolute;
    left: 297px; top: 28px;
    width: 1px; height: 166px;
    background: rgba(255,255,255,0.45);
  }
  .offer-copy {
    position: absolute;
    left: 322px;
    top: 30px;
    width: 260px;
  }
  .offer-headline {
    font-size: 19px;
    font-weight: 700;
    line-height: 21px;
    text-transform: uppercase;
  }
  .offer-body {
    margin-top: 5px;
    font-size: 16px;
    line-height: 20px;
    font-weight: 400;
  }
  .offer-url {
    margin-top: 7px;
    font-size: 19px;
    font-weight: 700;
  }
  .write-line {
    position: absolute;
    left: 36px;
    width: 520px;
    height: 1px;
    background: var(--ink);
  }
  .write-line.first { top: 260px; }
  .write-line.second { top: 300px; }
</style>
</head>
<body>
  <section class="card card-front">
    <div class="person-name">Dana Whitfield</div>
    <div class="contact-email">dana@larkwellnow.com</div>
    <div class="name-rule"></div>
    <div class="job-title">STORY MARKETING COACH</div>
    <div class="brand-dot"></div>
  </section>

  <section class="card card-back">
    <div class="offer-band">
      <div class="brand-lockup">
        <span class="lockup-dot"></span>
        <div class="brand-name">LARKWELL</div>
        <div class="brand-tagline">Tell stories that inspire action</div>
      </div>
      <div class="band-divider"></div>
      <div class="offer-copy">
        <p class="offer-headline">Reach more people.<br>Make more money.<br>Create more impact.</p>
        <p class="offer-body">Get your free Larkwell<br>Starter Package and our<br>marketing guide today at</p>
        <p class="offer-url">Larkwellnow.com/start</p>
      </div>
    </div>
    <div class="write-line first"></div>
    <div class="write-line second"></div>
  </section>
</body>
</html>
```